Business Card Design

Hi I need a business card designed, we already have the business name logo artwork and would like some concept ideas for the Bus Card layout.
On the back of the card i want to include the products and services that we offer.
We are a Plastics Sheeting manufacture based in Perth Australia.

                                       

We need a BC design for a company called Tarvo Plastics based in Perth Australia.

We supply from DIY to Trade & Industrial  Engineering Markets.

We specialise in:

·         Cut to size panels  (all shapes and sizes)

·         Plastics fabrication & Welding

·         Custom Designs

·         Plastic Repairs

·         PVC Pipe Slotting & PVC Pipe Threading

·         Supplier of all types of engineering plastics and profiles.

Including:           Acrylic / Clarvene

                               Polycarbonate / Dorvil

                               Prismatic Light Diffuser

                               Vantrib

                               HDPE / UHMWPE

                               PVC / PVC Foam

                               Nylon

                               HIPS

```html
<!DOCTYPE html>
<html lang="en">
<head>
<meta charset="utf-8">
<title>Tarvo Plastics – Business Card</title>
<link rel="stylesheet" href="https://fonts.googleapis.com/css2?family=Source+Sans+3:wght@400;600;700&display=swap">
<style>
  :root {
    --navy: #1c3568;
    --blue-dot: #2f7fc1;
    --orange: #e9821e;
    --red: #d42a2a;
    --yellow: #f3c316;
    --green: #6cb33f;
    --ink: #2b2b2b;
    --paper: #ffffff;
    --stage: #e7e5e1;
    --faint: #e8ecf3;
  }
  * { box-sizing: border-box; margin: 0; padding: 0; }
  html, body { width: 1200px; height: 720px; overflow: hidden; }
  body {
    background: var(--stage);
    font-family: "Source Sans 3", "Myriad Pro", Arial, sans-serif;
    color: var(--ink);
    position: relative;
  }
  .card {
    position: absolute;
    width: 540px;
    height: 330px;
    background: var(--paper);
    box-shadow: 0 4px 14px rgba(0,0,0,.18);
    overflow: hidden;
  }
  /* Front */
  .card--front { left: 40px; top: 195px; }
  .front__band {
    position: absolute; left: 0; top: 70px; bottom: 0; width: 78px;
    background: var(--navy);
  }
  .front__stripe { position: absolute; left: 120px; top: 92px; width: 400px; height: 6px; }
  .brand {
    position: absolute; left: 30px; top: 34px;
    display: flex; align-items: center; gap: 12px;
    background: var(--paper); padding: 6px 10px;
  }
  .brand__square { width: 30px; height: 30px; background: var(--navy); }
  .brand__name {
    font-weight: 700; font-size: 44px; line-height: 1; color: var(--navy);
    letter-spacing: .5px;
  }
  .person { position: absolute; right: 30px; top: 128px; text-align: right; }
  .person__name { font-weight: 700; font-size: 20px; color: var(--navy); }
  .person__title { font-size: 13px; color: var(--orange); }
  .contact {
    position: absolute; left: 96px; bottom: 24px;
    list-style: none; font-size: 14px; line-height: 1.45;
  }
  .contact__item { display: flex; align-items: center; gap: 6px; }
  .contact__icon { width: 11px; height: 11px; flex: none; }
  /* Back */
  .card--back { left: 620px; top: 195px; text-align: center; color: var(--navy); }
  .back__watermark {
    position: absolute; left: 0; right: 0; top: 140px;
    font-weight: 700; font-size: 72px; color: var(--faint); line-height: 1;
    white-space: nowrap; text-align: center;
  }
  .back__content { position: relative; padding: 22px 26px 0; }
  .back__intro { font-weight: 700; font-size: 15px; line-height: 1.25; }
  .back__heading { font-weight: 700; font-size: 20px; margin-top: 12px; }
  .back__list { font-size: 14px; color: var(--ink); line-height: 1.45; }
  .back__row { display: block; }
  .back__item { white-space: nowrap; margin: 0 5px; }
  .back__item::before {
    content: ""; display: inline-block; width: 6px; height: 6px; border-radius: 50%;
    background: var(--blue-dot); margin-right: 5px; vertical-align: middle;
  }
</style>
</head>
<body>

<section class="card card--front" aria-label="Business card front">
  <div class="front__band"></div>
  <svg class="front__stripe" viewBox="0 0 400 6" preserveAspectRatio="none" aria-hidden="true">
    <rect x="0" y="0" width="100" height="6" fill="var(--red)"/>
    <rect x="100" y="0" width="100" height="6" fill="var(--orange)"/>
    <rect x="200" y="0" width="100" height="6" fill="var(--yellow)"/>
    <rect x="300" y="0" width="100" height="6" fill="var(--green)"/>
  </svg>
  <div class="brand">
    <span class="brand__square"></span>
    <span class="brand__name">Tarvo Plastics</span>
  </div>
  <div class="person">
    <div class="person__name">Your Name</div>
    <div class="person__title">Title</div>
  </div>
  <ul class="contact">
    <li class="contact__item">
      <svg class="contact__icon" viewBox="0 0 12 12" aria-hidden="true"><circle cx="6" cy="6" r="5.2" fill="none" stroke="var(--orange)" stroke-width="1.4"/><path d="M4 3.5l1.2 1.3-.6.8c.5 1 1 1.5 1.9 1.9l.8-.6L8.6 8l-.8 1c-2.2-.5-3.8-2.1-4.3-4.3z" fill="var(--orange)"/></svg>
      08 5550 1842
    </li>
    <li class="contact__item">
      <svg class="contact__icon" viewBox="0 0 12 12" aria-hidden="true"><rect x="3" y="0.5" width="6" height="11" rx="1.2" fill="var(--orange)"/><rect x="4.2" y="2" width="3.6" height="6" fill="#fff"/></svg>
      0400 555 019
    </li>
    <li class="contact__item">
      <svg class="contact__icon" viewBox="0 0 12 12" aria-hidden="true"><rect x="1" y="4" width="10" height="7" rx="1" fill="var(--orange)"/><rect x="3" y="1" width="6" height="4" fill="var(--orange)"/><rect x="3.5" y="6.5" width="5" height="2" fill="#fff"/></svg>
      08 5550 1843
    </li>
    <li class="contact__item">
      <svg class="contact__icon" viewBox="0 0 12 12" aria-hidden="true"><rect x="0.5" y="2.5" width="11" height="7.5" rx="1" fill="var(--orange)"/><path d="M1 3l5 4 5-4" fill="none" stroke="#fff" stroke-width="1"/></svg>
      sales@tarvoplastics.com.au
    </li>
    <li>Unit 4/18 Orrin Circuit Halden Vale WA 6092</li>
    <li>PO Box 2270 Halden Vale DC WA 6981</li>
    <li>Kelmar Holdings Pty Ltd T/A Tarvo Plastics ABN: TBA</li>
  </ul>
</section>

<section class="card card--back" aria-label="Business card back">
  <div class="back__watermark" aria-hidden="true">Tarvo Plastics</div>
  <div class="back__content">
    <p class="back__intro">The Products And Services That We Offer<br>Are Supplied From Diy To Trade &amp; Industrial Engineering Markets</p>
    <h2 class="back__heading">We specialise in:</h2>
    <div class="back__list">
      <span class="back__row"><span class="back__item">Cut to size panels (all shapes and sizes)</span></span>
      <span class="back__row"><span class="back__item">Plastics fabrication &amp; Welding</span><span class="back__item">Custom Designs</span></span>
      <span class="back__row"><span class="back__item">Plastic Repairs</span><span class="back__item">PVC Pipe Slotting &amp; PVC Pipe Threading</span></span>
      <span class="back__row"><span class="back__item">Supplier of all types of engineering plastics and profiles</span></span>
    </div>
    <h2 class="back__heading">Including:</h2>
    <div class="back__list">
      <span class="back__row"><span class="back__item">Acrylic / Clarvene</span><span class="back__item">Polycarbonate / Dorvil</span></span>
      <span class="back__row"><span class="back__item">Prismatic Light Diffuser</span><span class="back__item">Vantrib</span><span class="back__item">HDPE / UHMWPE</span></span>
      <span class="back__row"><span class="back__item">PVC / PVC Foam</span><span class="back__item">Nylon</span><span class="back__item">HIPS</span></span>
    </div>
  </div>
</section>

</body>
</html>
```